Letter and Envelope Design For Harborline Realty

Please design a letter and an envelope incorporating our logo (See Attached). We are also launched a business card contest. Since we want them to match, please feel free to submit a design for both the business card and also the letter design and envelope.

Requirements
Must have
• The envelope, the letter and the business cards must match somehow connecting the designs. We want them to have something that holds them together besides the logo.

```html
<!DOCTYPE html>
<html lang="en">
<head>
<meta charset="utf-8">
<title>Harborline Realty – Letterhead and Envelopes</title>
<link href="https://fonts.googleapis.com/css2?family=Source+Sans+3:wght@400;600;700&display=swap" rel="stylesheet">
<style>
  :root {
    --navy: #0b1a8e;
    --ink: #3d3d3d;
    --paper: #f8f8f8;
    --backdrop: #e4e4e4;
    --rule: #8a8a8a;
    --placeholder: #e6e6e6;
  }
  * { margin: 0; padding: 0; box-sizing: border-box; }
  html, body { width: 1200px; height: 825px; overflow: hidden; }
  body {
    background: var(--backdrop);
    font-family: "Source Sans 3", Arial, sans-serif;
    color: var(--ink);
    position: relative;
  }
  .sheet { position: absolute; background: var(--paper); overflow: hidden; }

  /* Brand name set as plain text */
  .brand {
    position: absolute; text-align: center; color: var(--navy);
    font-weight: 600; font-size: 14px; letter-spacing: 2px; line-height: 16px;
  }

  /* Letterhead */
  .letter { left: 80px; top: 84px; width: 464px; height: 656px; }
  .letter .brand { left: 30px; top: 82px; width: 128px; }

  .letter-body { position: absolute; left: 36px; top: 142px; width: 394px; }
  .salutation { font-size: 11.5px; font-weight: 700; margin-bottom: 12px; color: #444; }
  .letter-body p {
    font-size: 9.7px; line-height: 12.2px; text-align: justify; margin-bottom: 12px;
  }
  .signature {
    position: absolute; left: 36px; top: 432px; width: 90px; height: 44px;
    background: var(--placeholder); border-radius: 4px;
  }

  /* Contact footer shared by letter and envelope */
  .contact { position: absolute; height: 44px; }
  .contact .accent-bar { position: absolute; left: 0; top: 0; width: 6px; height: 100%; background: var(--navy); }
  .contact .lines { position: absolute; left: 11px; top: 2px; font-size: 6.8px; line-height: 9.6px; color: #333; white-space: nowrap; }
  .contact .company { color: var(--navy); font-weight: 700; }
  .contact .label { color: var(--navy); font-weight: 700; }
  .contact .rule { position: absolute; left: 11px; top: 29px; height: 1px; background: var(--rule); }
  .contact .web {
    position: absolute; top: 24px; height: 11px; padding: 0 9px;
    background: var(--navy); color: #fff; font-size: 7.4px; line-height: 11px; letter-spacing: .3px;
    clip-path: polygon(5px 0, calc(100% - 3px) 0, 100% 50%, calc(100% - 5px) 100%, 5px 100%, 0 50%);
  }
  .letter .contact { left: 36px; top: 612px; width: 396px; }
  .letter .contact .rule { width: 300px; }
  .letter .contact .web { right: 0; }

  /* Envelope front */
  .envelope-front { left: 586px; top: 238px; width: 534px; height: 232px; }
  .envelope-front .brand { left: 24px; top: 56px; width: 124px; }
  .envelope-front .contact { left: 34px; top: 190px; width: 466px; height: 42px; }
  .envelope-front .contact .rule { width: 370px; }
  .envelope-front .contact .web { right: 0; }

  /* Envelope back */
  .envelope-back { left: 586px; top: 508px; width: 534px; height: 232px; }
  .envelope-back .flap { position: absolute; left: 0; top: 0; }
  .flap-name {
    position: absolute; left: 0; top: 20px; width: 100%; text-align: center;
    color: #fff; font-weight: 600; font-size: 11px; letter-spacing: 2px;
  }
</style>
</head>
<body>

<section class="sheet letter" aria-label="Letterhead">
  <div class="brand">HARBORLINE<br>REALTY</div>

  <div class="letter-body">
    <p class="salutation">Dear Mr. John,</p>
    <p>Lorem Ipsum is simply dummy text of the printing and typesetting industry. Lorem Ipsum has been the industry's standard dummy text ever since the 1500s, when an unknown printer took a galley of type and scrambled it to make a type specimen book. It has survived not only five centuries, but also the leap into electronic typesetting, remaining essentially unchanged.</p>
    <p>The standard chunk of Lorem Ipsum used since the 1500s is reproduced below for those interested. Sections 1.10.32 and 1.10.33 from "de Finibus Bonorum et Malorum" by Cicero are also reproduced in their exact original form, accompanied by English versions from the 1914 translation by H. Rackham</p>
    <p>Lorem Ipsum is simply dummy text of the printing and typesetting industry. Lorem Ipsum has been the industry's standard dummy text ever since the 1500s, when an unknown printer took a galley of type and scrambled it to make a type specimen book. It has survived not only five centuries, but also the leap into electronic typesetting, remaining essentially unchanged. It was popularised in the</p>
    <p>Lorem Ipsum is simply dummy text of the printing and typesetting industry. Lorem Ipsum has been the industry's standard dummy text ever since the 1500s, when an unknown printer took a galley of type and scrambled it to make a type specimen book. It has survived not only five centuries, but also the leap into electronic typesetting, remaining essentially unchanged. It was popularised in the</p>
  </div>

  <div class="signature" role="img" aria-label="Handwritten signature of the sender"></div>

  <div class="contact">
    <span class="accent-bar"></span>
    <div class="lines">
      <div class="company">Harborline Realty</div>
      <div>Po. box 201, Street Name, City Name, Zip Code - 00000</div>
      <div><span class="label">Tel:</span> 555-014-2290 &nbsp;<span class="label">Mail:</span> info@harborlinerealty.com</div>
    </div>
    <span class="rule"></span>
    <span class="web">www.harborline.com</span>
  </div>
</section>

<section class="sheet envelope-front" aria-label="Envelope front">
  <div class="brand">HARBORLINE<br>REALTY</div>
  <div class="contact">
    <span class="accent-bar"></span>
    <div class="lines">
      <div class="company">Harborline Realty</div>
      <div>Po. box 201, Street Name, City Name, Zip Code - 00000</div>
      <div><span class="label">Tel:</span> 555-014-2290 &nbsp;<span class="label">Mail:</span> info@harborlinerealty.com</div>
    </div>
    <span class="rule"></span>
    <span class="web">www.harborline.com</span>
  </div>
</section>

<section class="sheet envelope-back" aria-label="Envelope back">
  <svg class="flap" width="534" height="60" viewBox="0 0 534 60" aria-hidden="true">
    <path d="M0 0 H534 L531 36 Q529 44 518 46 Q267 58 16 46 Q4 44 3 36 Z" fill="var(--navy)"/>
  </svg>
  <div class="flap-name">HARBORLINE</div>
</section>

</body>
</html>
```